Business card design needed

Family General Practitioner/ Family Physician.
Logo is the logo of the Noble Guild of Family Healers Oceania
http://kpltw.varendo.example/ImageShelf/marks/pages/NGFHO%20mark_jpg.htm
Updates

Project Deadline Extended
Reason: Just a bit more time to make changes and the weekend for me to look at things closely and to choose. Thanks, Orin

Thanks for all the submissions. So many of them are really works of art. Not one of them are not good. The ones that I am eliminating are the ones that I think are not suitable for me personally only, and because if I don't, it makes it very difficult to decide as many of you are also sending me slight variations of a card. I have just decided to choose a second place card too. Can't thank you all enough. Good luck, Orin. P.S - Working today till 10 pm as the card says :-), so probably won't be able to give a feedback till late Saturday night or Sunday morning here in Sydney, Australia. 

Project Deadline Extended
Reason: Just added a second place to the budget and realised that Australia is ahead of the rest of the world in the time zone (only :-) - don't want to offend anyone or start a debate!! ) , so Monday deadline will mean it will be a weekend for the rest of the world. Just wanted to give everyone more time to submit their best, especially since I will be picking a second card too. Can't thank everyone enough for the submissions. P.S - Not keen on photos on the card.

Industry/Entity Type

Business

Contact Information for Business Card

Dr. Orin Halvey M.B.B.S., F.N.G.F.H.O
Family General Practitioner
Address, timings, phone and fax number on the back.

Requirements
Must have
• Timings
Mon 7 am - 7 pm
Tues 7 am - 12 pm
Wed 7 am - 10 pm
Thurs 7 am - 12 pm
Fri 7 am - 8 pm
Sat 8 am - 10 pm
Sun - Off

```html
<!DOCTYPE html>
<html lang="en">
<head>
<meta charset="utf-8">
<title>Working Hours Card</title>
<link href="https://fonts.googleapis.com/css2?family=Archivo+Narrow:wght@400;700&display=swap" rel="stylesheet">
<style>
  :root {
    --backdrop: #ede6d3;
    --card-navy: #2c4466;
    --band-blue: #2f5381;
    --title-khaki: #a89c80;
    --label-cream: #cfc8ad;
    --bar-orange: #f39322;
  }
  * { margin: 0; padding: 0; box-sizing: border-box; }
  html, body {
    width: 1200px; height: 960px; overflow: hidden;
    background: var(--backdrop);
    font-family: "Archivo Narrow", "Arial Narrow", sans-serif;
  }
  .card {
    position: absolute; left: 138px; top: 219px;
    width: 924px; height: 521px;
    background: var(--card-navy);
    border-radius: 30px; overflow: hidden;
  }
  .card-title {
    position: absolute; left: 0; right: 0; top: 26px;
    text-align: center; font-weight: 700; font-size: 31px;
    letter-spacing: 0.3px; color: var(--title-khaki);
  }
  .hour-mark {
    position: absolute; top: 78px; font-size: 24px;
    color: var(--label-cream);
  }
  .day-label {
    position: absolute; left: 82px; font-size: 27px;
    color: var(--label-cream); transform: translateY(-50%);
  }
  .hours-bar {
    position: absolute; height: 11px; background: var(--bar-orange);
    transform: translateY(-50%);
  }
  .contact-band {
    position: absolute; left: 0; right: 0; bottom: 0; height: 107px;
    background: var(--band-blue);
  }
  .address {
    position: absolute; left: 0; right: 0; top: 18px;
    text-align: center; font-size: 25px; color: var(--label-cream);
  }
  .contact-line {
    position: absolute; top: 57px; font-size: 25px; color: var(--bar-orange);
  }
</style>
</head>
<body>
  <div class="card">
    <h1 class="card-title">WORKING HOURS</h1>

    <span class="hour-mark" style="left:260px">7A</span>
    <span class="hour-mark" style="left:291px">8A</span>
    <span class="hour-mark" style="left:642px">7P</span>
    <span class="hour-mark" style="left:674px">8P</span>
    <span class="hour-mark" style="left:737px">10P</span>
    <span class="hour-mark" style="left:801px">12P</span>

    <span class="day-label" style="top:130px">Monday</span>
    <span class="day-label" style="top:170px">Tuesday</span>
    <span class="day-label" style="top:210px">Wednesday</span>
    <span class="day-label" style="top:250px">Thursday</span>
    <span class="day-label" style="top:291px">Friday</span>
    <span class="day-label" style="top:332px">Saturday</span>
    <span class="day-label" style="top:373px">Sunday</span>

    <div class="hours-bar" style="top:130px;left:260px;width:383px"></div>
    <div class="hours-bar" style="top:170px;left:260px;width:543px"></div>
    <div class="hours-bar" style="top:210px;left:260px;width:479px"></div>
    <div class="hours-bar" style="top:250px;left:260px;width:543px"></div>
    <div class="hours-bar" style="top:291px;left:260px;width:416px"></div>
    <div class="hours-bar" style="top:331px;left:292px;width:447px"></div>

    <div class="contact-band">
      <p class="address">Upper Level, Lantern Court, Harbourview Shopping Centre, Bellmont Hill, NSW 2999</p>
      <p class="contact-line" style="left:145px">PHONE: 02 5550 1400</p>
      <p class="contact-line" style="left:550px">FAX: 02 5550 1233</p>
    </div>
  </div>
</body>
</html>
```